Design a website for a newly developed Delta 8 THC Company

Design a responsive Website with the following goals in mind:
- Built on Wordpress/WooCommerce theme. Please use this when designing for ease of integration.
- Build trust with website visitors with an engaging, informative content driven website, that leads to a conversion of product purchase and repeat business. We will also be driving consumers to businesses that carry our products as well.
- The website will embody a lifestyle feel and make the visitor identify with the content.
- The website will allow for super charged SEO and other digital marketing and advertising strategies and tactics used to increase discovery, awareness, and conversion.
Please see additional goals in the uploaded files.
Target Market(s)
Male/Female 21-
Industry/Entity Type
Cannabis/Hemp
Coding
Coded - Design and coding required
Number of Pages Required
5+ page
Font styles to use
Other font styles liked:
- Montserrat
Look and feel
Each slider illustrates characteristics of the customer's brand and the style your logo design should communicate.

```html
<!DOCTYPE html>
<html lang="en">
<head>
<meta charset="utf-8">
<title>Aurelo – Delta 8</title>
<link rel="stylesheet" href="https://fonts.googleapis.com/css2?family=Montserrat:wght@400;500;600&family=Poppins:wght@700&family=Lora:wght@400&display=swap">
<style>
:root{
  --green:#8db650;
  --green-soft:#d9efbd;
  --ink:#111;
  --muted:#666;
  --gold:#b9985a;
  --panel:#f3f3f3;
  --line:#e4e4e4;
  --white:#fff;
}
*{margin:0;padding:0;box-sizing:border-box}
html,body{width:1200px;height:3550px;overflow:hidden;background:var(--white)}
body{position:relative;font-family:"Lora",serif;color:var(--ink)}
.abs{position:absolute}
.serif-link{font-family:"Lora",serif;font-size:13px;color:#555;text-decoration:none}
.top-links a{position:absolute;top:56px}
.brand{position:absolute;display:flex;align-items:center;gap:8px;font-family:"Lora",serif;color:var(--gold);letter-spacing:5px}
.brand .dot{width:14px;height:14px;border-radius:50%;background:var(--gold)}
.header-brand{left:537px;top:48px;font-size:24px}
.icon-btn{position:absolute;top:50px}
.cart-badge{position:absolute;left:1091px;top:49px;width:9px;height:9px;border-radius:50%;background:var(--green)}
.nav-rule{position:absolute;left:97px;width:1006px;top:128px;border-top:1px solid var(--line)}
.main-nav a{position:absolute;top:140px}
.main-nav a.active{color:var(--green)}
.hero{position:absolute;left:97px;top:167px;width:1006px;height:505px;background:linear-gradient(90deg,#fafafa,#f0f0f0 30%,#fff);box-shadow:0 6px 18px rgba(0,0,0,.12);overflow:hidden}
.hero h1{position:absolute;left:78px;top:80px;font-family:"Montserrat",sans-serif;font-weight:600;font-size:68px}
.hero p{position:absolute;left:78px;top:166px;width:420px;font-family:"Montserrat",sans-serif;font-size:18.5px;line-height:25px}
.btn{display:flex;align-items:center;justify-content:center;background:var(--green);color:var(--white);font-family:"Lora",serif;font-size:13px}
.hero .btn{position:absolute;left:78px;top:257px;width:153px;height:41px}
.hero-arrows{position:absolute;left:81px;top:377px;display:flex;gap:8px}
.hero-arrows span{width:33px;height:33px;border:1.5px solid var(--green);display:flex;align-items:center;justify-content:center}
.hero-visual{position:absolute;left:496px;top:0;width:490px;height:505px;background:radial-gradient(circle at 50% 50%,#4f8a2c 0,#6aa83a 38%,#a6cf7d 58%,rgba(255,255,255,0) 72%)}
.features .feature{position:absolute;top:736px;width:180px;text-align:center;font-family:"Montserrat",sans-serif;font-size:13.5px;color:#333}
.features svg{display:block;margin:0 auto 12px}
.section-title{font-family:"Poppins",sans-serif;font-weight:700;font-size:38px}
.products-title{position:absolute;left:97px;top:900px}
.next-btn{position:absolute;left:950px;top:910px;width:153px;height:40px}
.product{position:absolute;width:325px;height:344px;background:var(--white);box-shadow:0 4px 16px rgba(0,0,0,.12)}
.product .ph{position:absolute;left:70px;top:30px;width:185px;height:200px;border-radius:6px}
.product .name{position:absolute;left:26px;top:245px;font-family:"Montserrat",sans-serif;font-weight:500;font-size:17.5px}
.product .price{position:absolute;left:26px;top:271px;font-family:"Montserrat",sans-serif;font-size:17px;color:var(--green)}
.qty{position:absolute;left:26px;top:305px;display:flex}
.qty span{width:33px;height:30px;border:1px solid var(--green);display:flex;align-items:center;justify-content:center;font-family:"Montserrat",sans-serif;font-size:12px;color:var(--green)}
.qty span.n{background:var(--green);color:var(--white);font-weight:600}
.bag{position:absolute;right:7px;top:302px;width:36px;height:36px;border-radius:50%;background:var(--green);display:flex;align-items:center;justify-content:center}
.bundle{position:absolute;left:97px;top:1778px;width:1006px;height:649px;background:var(--panel)}
.bundle .section-title{position:absolute;left:0;width:100%;top:68px;text-align:center}
.bundle-card{position:absolute;top:140px;width:422px;height:371px;background:var(--white);box-shadow:0 4px 16px rgba(0,0,0,.1);text-align:center}
.bundle-card .ph{position:absolute;left:75px;top:25px;width:272px;height:262px;border-radius:8px}
.bundle-card .name{position:absolute;left:0;width:100%;top:290px;font-family:"Montserrat",sans-serif;font-weight:500;font-size:22px}
.bundle-card .price{position:absolute;left:0;width:100%;top:326px;font-family:"Montserrat",sans-serif;font-size:17px;color:var(--green)}
.view-all{position:absolute;left:427px;top:532px;width:151px;height:41px}
.insta-title{position:absolute;left:0;width:1200px;top:2483px;text-align:center}
.insta .shot{position:absolute;top:2556px;width:245px;height:236px}
.newsletter{position:absolute;left:0;top:2876px;width:1200px;height:316px;background:var(--green);color:var(--white);text-align:center}
.newsletter .section-title{position:absolute;left:0;width:100%;top:70px}
.newsletter p{position:absolute;left:170px;width:860px;top:135px;font-size:12.5px;line-height:22px}
.subscribe{position:absolute;left:205px;top:197px;display:flex;box-shadow:0 6px 14px rgba(0,0,0,.12)}
.subscribe .field{width:636px;height:39px;background:var(--white);color:#777;font-size:12.5px;text-align:left;padding:11px 20px}
.subscribe .go{width:154px;height:39px;background:var(--green);font-size:12.5px;display:flex;align-items:center;justify-content:center}
.footer-brand{left:97px;top:3320px;font-size:20px}
.footer h4{position:absolute;top:3283px;font-family:"Montserrat",sans-serif;font-weight:500;font-size:18px}
.footer ul{position:absolute;top:3328px;list-style:none}
.footer li{font-size:13px;color:#777;line-height:25px}
.social li{display:flex;align-items:center;gap:8px}
.social i{width:9px;height:9px;background:var(--green);border-radius:2px;display:inline-block}
.copyright{position:absolute;left:0;width:1200px;top:3508px;text-align:center;font-size:10.5px;color:#666}
</style>
</head>
<body>

<header>
  <nav class="top-links">
    <a class="serif-link" style="left:100px" href="#">Wishlist</a>
    <a class="serif-link" style="left:198px" href="#">Track order</a>
    <a class="serif-link" style="left:318px" href="#">New Arrivals</a>
  </nav>
  <div class="brand header-brand"><span class="dot"></span>AURELO</div>
  <svg class="icon-btn" style="left:1023px" width="22" height="22" viewBox="0 0 22 22" fill="none" stroke="#222" stroke-width="1.8"><circle cx="9" cy="9" r="7"/><path d="M14 14l6 6"/></svg>
  <svg class="icon-btn" style="left:1075px" width="24" height="22" viewBox="0 0 24 22" fill="none" stroke="#222" stroke-width="1.6"><path d="M1 2h4l3 12h11l3-9H6"/><circle cx="9" cy="19" r="1.6"/><circle cx="18" cy="19" r="1.6"/></svg>
  <span class="cart-badge"></span>
  <div class="nav-rule"></div>
  <nav class="main-nav">
    <a class="serif-link active" style="left:137px" href="#">Home</a>
    <a class="serif-link" style="left:235px" href="#">About Us</a>
    <a class="serif-link" style="left:353px" href="#">Products</a>
    <a class="serif-link" style="left:470px" href="#">Categories</a>
    <a class="serif-link" style="left:598px" href="#">Blog</a>
    <a class="serif-link" style="left:686px" href="#">Gallery</a>
    <a class="serif-link" style="left:790px" href="#">Reviews</a>
    <a class="serif-link" style="left:902px" href="#">Gifts</a>
    <a class="serif-link" style="left:993px" href="#">Contact Us</a>
  </nav>
</header>

<section class="hero">
  <h1>Delta 8</h1>
  <p>Lorem ipsum dolor sit amet, consectetur adipiscing elit, sed do eiusmod</p>
  <a class="btn" href="#">Read More</a>
  <div class="hero-arrows">
    <span><svg width="10" height="10" viewBox="0 0 10 10" fill="none" stroke="#8db650" stroke-width="1.5"><path d="M7 1L3 5l4 4"/></svg></span>
    <span><svg width="10" height="10" viewBox="0 0 10 10" fill="none" stroke="#8db650" stroke-width="1.5"><path d="M3 1l4 4-4 4"/></svg></span>
  </div>
  <div class="hero-visual" role="img" aria-label="Potted hemp plant seen from above"></div>
</section>

<section class="features">
  <div class="feature" style="left:135px">
    <svg width="80" height="72" viewBox="0 0 80 72"><path d="M10 66C14 30 40 10 76 8 70 44 46 62 16 58Z" fill="#d9efbd"/><path d="M8 68C24 48 40 34 60 22" stroke="#fff" stroke-width="3" fill="none"/></svg>
    100% Organic</div>
  <div class="feature" style="left:325px">
    <svg width="72" height="72" viewBox="0 0 72 72"><circle cx="36" cy="36" r="34" fill="#d9efbd"/><path d="M21 37l10 10 20-22" stroke="#fff" stroke-width="6" fill="none" stroke-linecap="round"/></svg>
    100% Gurantee</div>
  <div class="feature" style="left:516px">
    <svg width="60" height="80" viewBox="0 0 60 80"><path d="M30 2C22 22 4 38 4 54a26 26 0 0 0 52 0C56 38 38 22 30 2Z" fill="#d9efbd"/><path d="M16 52a14 14 0 0 0 12 16" stroke="#fff" stroke-width="4" fill="none"/></svg>
    3rd party Tested</div>
  <div class="feature" style="left:707px">
    <svg width="76" height="76" viewBox="0 0 76 76"><circle cx="38" cy="38" r="37" fill="#d9efbd"/></svg>
    &lt;3% THC</div>
  <div class="feature" style="left:897px">
    <svg width="76" height="76" viewBox="0 0 76 76"><circle cx="38" cy="38" r="37" fill="#d9efbd"/></svg>
    NON GMO</div>
</section>

<h2 class="section-title products-title">Popular Products</h2>
<a class="btn next-btn" href="#">Next</a>

<section class="product-grid">
  <article class="product" style="left:97px;top:976px">
    <div class="ph" role="img" aria-label="Silver vape mod with tank" style="background:linear-gradient(160deg,#e8e8e8,#9a9a9a 60%,#333)"></div>
    <div class="name">Product Name</div><div class="price">$52.00</div>
    <div class="qty"><span>‹</span><span class="n">2</span><span>›</span></div>
    <div class="bag"><svg width="16" height="16" viewBox="0 0 16 16" fill="none" stroke="#fff" stroke-width="1.5"><rect x="2" y="5" width="12" height="10" rx="1"/><path d="M5 5V3a3 3 0 0 1 6 0v2"/></svg></div>
  </article>
  <article class="product" style="left:438px;top:976px">
    <div class="ph" role="img" aria-label="Clear pouch of fruit gummies" style="background:linear-gradient(150deg,#ddd,#e8b04a 45%,#c94a3a 65%,#555)"></div>
    <div class="name">Product Name</div><div class="price">$52.00</div>
    <div class="qty"><span>‹</span><span class="n">2</span><span>›</span></div>
    <div class="bag"><svg width="16" height="16" viewBox="0 0 16 16" fill="none" stroke="#fff" stroke-width="1.5"><rect x="2" y="5" width="12" height="10" rx="1"/><path d="M5 5V3a3 3 0 0 1 6 0v2"/></svg></div>
  </article>
  <article class="product" style="left:779px;top:976px">
    <div class="ph" role="img" aria-label="Black vape mod with branded label" style="background:linear-gradient(170deg,#eee,#555 40%,#222)"></div>
    <div class="name">Product Name</div><div class="price">$52.00</div>
    <div class="qty"><span>‹</span><span class="n">2</span><span>›</span></div>
    <div class="bag"><svg width="16" height="16" viewBox="0 0 16 16" fill="none" stroke="#fff" stroke-width="1.5"><rect x="2" y="5" width="12" height="10" rx="1"/><path d="M5 5V3a3 3 0 0 1 6 0v2"/></svg></div>
  </article>
  <article class="product" style="left:97px;top:1338px">
    <div class="ph" role="img" aria-label="Pair of silver vape pens" style="background:linear-gradient(160deg,#f2f2f2,#b5b5b5 55%,#555)"></div>
    <div class="name">Product Name</div><div class="price">$52.00</div>
    <div class="qty"><span>‹</span><span class="n">2</span><span>›</span></div>
    <div class="bag"><svg width="16" height="16" viewBox="0 0 16 16" fill="none" stroke="#fff" stroke-width="1.5"><rect x="2" y="5" width="12" height="10" rx="1"/><path d="M5 5V3a3 3 0 0 1 6 0v2"/></svg></div>
  </article>
  <article class="product" style="left:438px;top:1338px">
    <div class="ph" role="img" aria-label="Black foil sachet" style="background:linear-gradient(160deg,#fff 20%,#222 50%,#111 65%,#fff 85%)"></div>
    <div class="name">Product Name</div><div class="price">$52.00</div>
    <div class="qty"><span>‹</span><span class="n">2</span><span>›</span></div>
    <div class="bag"><svg width="16" height="16" viewBox="0 0 16 16" fill="none" stroke="#fff" stroke-width="1.5"><rect x="2" y="5" width="12" height="10" rx="1"/><path d="M5 5V3a3 3 0 0 1 6 0v2"/></svg></div>
  </article>
  <article class="product" style="left:779px;top:1338px">
    <div class="ph" role="img" aria-label="Pile of colourful gummy cubes" style="background:linear-gradient(120deg,#f5d23a,#e84c4c 30%,#7cc14a 55%,#4aa3e0 75%,#f09a3a)"></div>
    <div class="name">Product Name</div><div class="price">$52.00</div>
    <div class="qty"><span>‹</span><span class="n">2</span><span>›</span></div>
    <div class="bag"><svg width="16" height="16" viewBox="0 0 16 16" fill="none" stroke="#fff" stroke-width="1.5"><rect x="2" y="5" width="12" height="10" rx="1"/><path d="M5 5V3a3 3 0 0 1 6 0v2"/></svg></div>
  </article>
</section>

<section class="bundle">
  <h2 class="section-title">Popular Bundle Pack</h2>
  <article class="bundle-card" style="left:71px">
    <div class="ph" role="img" aria-label="Black gummy bag with lemons" style="background:linear-gradient(170deg,#333,#111 65%,#e8d84a)"></div>
    <div class="name">Product Name</div><div class="price">$52.00</div>
  </article>
  <article class="bundle-card" style="left:514px">
    <div class="ph" role="img" aria-label="Silver gummy bag with watermelon" style="background:linear-gradient(170deg,#eee,#bbb 60%,#d2443c 80%,#3b6e2a)"></div>
    <div class="name">Product Name</div><div class="price">$52.00</div>
  </article>
  <a class="btn view-all" href="#">View All</a>
</section>

<h2 class="section-title insta-title">Instagram</h2>
<section class="insta">
  <div class="shot" style="left:97px" role="img" aria-label="Gummy bears on a table" style="background:#b65"></div>
  <div class="shot" style="left:351px;background:linear-gradient(135deg,#e84a3a,#f4b040 50%,#6a7a3a)" role="img" aria-label="Gummy bears with hemp buds"></div>
  <div class="shot" style="left:604px;background:linear-gradient(135deg,#eee,#888 45%,#d76a2a 70%,#222)" role="img" aria-label="Vape pens and tincture bottles"></div>
  <div class="shot" style="left:857px;background:linear-gradient(135deg,#ddd,#999 50%,#333)" role="img" aria-label="Man exhaling vapour"></div>
</section>
<style>.insta .shot:first-child{background:linear-gradient(135deg,#8a6a5a,#e8c04a 40%,#d43a2a 65%,#ddd)}</style>

<section class="newsletter">
  <h2 class="section-title">Sign Up Our Newsletter</h2>
  <p>Lorem ipsum dolor sit amet, consectetur adipiscing elit, sed do eiusmod tempor incididunt ut labore et dolore magna aliqua. Ut enim ad minim veniam, quis nostrud exercitation ullamco laboris nisi ut aliquip ex ea commodo consequat.</p>
  <div class="subscribe"><div class="field">Enter Your Email Address</div><div class="go">Subscribe Now</div></div>
</section>

<footer class="footer">
  <div class="brand footer-brand"><span class="dot"></span>AURELO</div>
  <h4 style="left:349px">Links</h4>
  <ul style="left:350px"><li>Home</li><li>About Us</li><li>Products</li><li>Categories</li><li>Blog</li></ul>
  <ul style="left:553px"><li>Gallery</li><li>Reviews</li><li>Gifts</li><li>Contact Us</li></ul>
  <h4 style="left:755px">Others</h4>
  <ul style="left:756px"><li>Wishlist</li><li>Track Order</li><li>New arrival</li><li>Delivery</li><li>Return</li></ul>
  <h4 style="left:1010px">Follow Us</h4>
  <ul class="social" style="left:1011px"><li><i></i>Facebook</li><li><i></i>Twitter</li><li><i></i>Youtube</li><li><i></i>linked In</li><li><i></i>Instagram</li></ul>
  <div class="copyright">© Copyrights 2020 The Company Name. All rights reserved.</div>
</footer>

</body>
</html>
```